13 Varno - new website design project

Our company Varno Electrical is developing a new lead generation website focused on Electrical, LED Lighting and Solar Power. We need a high converting website.

Example of our current website is www.varnoelectrical-example.com.au You can take content from this website for this new design. Our colours are red, black and white. For our new website we would like to promote Varno, Spark Every Day. Please listen to the jingle.

The below link is the company jingle that we have developed.
http://www.tunecraftdemo.com.au/vrn-tc-v1/

The key for this brief is to generate leads for Electrical, LED Lighting (for commercial) and Solar Power & Storage.

Target Market(s)

Business owners in Melbourne Victoria

Number of Pages Required

4 page

Colors
ec1f27
ffffff

Requirements
Must have
• This page must be clean, be in line with company branding and a high converting lead website.

```html
<!DOCTYPE html>
<html lang="en">
<head>
<meta charset="utf-8">
<title>Varno Electrical – Electrical, LED Lighting, Solar Power</title>
<link rel="stylesheet" href="https://fonts.googleapis.com/css2?family=Exo+2:wght@500;600;700&family=Lato:ital,wght@0,400;0,700;1,400&family=Montserrat:wght@500;600&family=Pathway+Gothic+One&display=swap">
<style>
:root{
  --red:#d1222b;
  --red-bright:#ec1f27;
  --ink:#1d1d1f;
  --grey-text:#6b6b6b;
  --white:#ffffff;
  --navy:#17132b;
  --navy-deep:#0f0c1f;
  --star:#f4c21a;
}
*{margin:0;padding:0;box-sizing:border-box}
html,body{width:1200px;height:2635px;overflow:hidden;background:var(--white)}
body{position:relative;font-family:"Lato",sans-serif;color:var(--ink)}
.abs{position:absolute}

/* Header */
.site-header{position:absolute;left:0;top:0;width:1200px;height:104px;background:var(--white);z-index:5}
.brand{position:absolute;left:78px;top:30px;display:flex;align-items:center;gap:12px}
.brand-dot{width:34px;height:34px;border-radius:50%;background:var(--red)}
.brand-name{font-family:"Exo 2",sans-serif;font-weight:700;font-size:40px;color:var(--ink);letter-spacing:1px}
.main-nav{position:absolute;top:0;left:0;width:100%;height:104px}
.main-nav a{position:absolute;top:44px;font-family:"Montserrat",sans-serif;font-weight:500;font-size:15px;color:var(--ink);text-decoration:none;letter-spacing:.3px;white-space:nowrap}
.main-nav a.active{color:var(--red)}
.main-nav a.active::before{content:"";position:absolute;left:-4px;right:-4px;top:-44px;height:4px;background:var(--red)}

/* Hero */
.hero{position:absolute;left:0;top:104px;width:1200px;height:580px;background:linear-gradient(180deg,#5d6b74 0%,#a9b8c0 45%,#d7e1e6 70%,#9fb0ba 100%)}
.hero-photo{position:absolute;inset:0}
.hero-banner{position:absolute;left:222px;top:180px;width:755px;height:160px;background:rgba(25,25,28,.72);clip-path:polygon(6% 0,100% 0,94% 100%,0 100%)}
.hero-stripe{position:absolute;left:942px;top:172px;width:60px;height:186px;background:var(--red);clip-path:polygon(60% 0,100% 0,40% 100%,0 100%)}
.hero-title{position:absolute;left:0;width:1200px;top:196px;text-align:center;font-family:"Pathway Gothic One",sans-serif;font-weight:400;font-size:60px;line-height:72px;color:var(--white)}
.hero-sub{position:absolute;left:0;width:1200px;top:286px;text-align:center;font-family:"Montserrat",sans-serif;font-weight:500;font-size:20px;line-height:26px;color:var(--white)}

/* Welcome */
.welcome-band{position:absolute;left:0;top:594px;width:1200px;height:460px;background:linear-gradient(90deg,#dcdcdc,#f1f1f1 55%,#ececec);clip-path:polygon(0 0,100% 88px,100% 355px,0 452px)}
.welcome-photo{position:absolute;left:0;top:600px;width:560px;height:450px;background:radial-gradient(ellipse at 50% 50%,#f7f7f5 0%,#e2dfd6 45%,#c9c4b4 75%,rgba(220,220,220,0) 100%);clip-path:polygon(0 0,100% 80px,100% 370px,0 446px)}
.welcome-edge{position:absolute;left:0;top:588px;width:1200px;height:100px}
.welcome-title{position:absolute;left:589px;top:696px;font-family:"Exo 2",sans-serif;font-weight:600;font-size:41px;color:var(--ink)}
.welcome-title span{color:var(--red)}
.welcome-text{position:absolute;left:590px;top:762px;width:520px;font-size:13.5px;line-height:23.5px;color:var(--grey-text)}
.btn{display:inline-block;background:var(--red);color:var(--white);font-family:"Lato",sans-serif;font-weight:700;font-size:15px;text-align:center;text-decoration:none}
.btn-welcome{position:absolute;left:587px;top:880px;width:146px;height:51px;line-height:51px}

/* Services */
.section-title{position:absolute;left:0;width:1200px;text-align:center;font-family:"Exo 2",sans-serif;font-weight:600;color:var(--red)}
.services-title{top:1040px;font-size:44px}
.service-card{position:absolute;top:1124px;width:334px;height:334px;overflow:hidden}
.service-card .visual{position:absolute;inset:0}
.card-electrical{left:77px}
.card-electrical .visual{background:linear-gradient(135deg,#8a8f94,#c9b79a 55%,#efe5c8)}
.card-led{left:434px}
.card-led .visual{background:radial-gradient(circle at 55% 45%,#ffffff,#e3e3e5 55%,#c6c8cc)}
.card-solar{left:789px}
.card-solar .visual{background:linear-gradient(180deg,#4f79b4 0%,#b7bdd0 30%,#f1c7a3 42%,#33507f 50%,#1c3565 100%)}
.service-panel{position:absolute;left:0;bottom:0;width:100%;background:rgba(200,25,35,.88);color:var(--white)}
.service-panel h3{font-family:"Lato",sans-serif;font-weight:700;font-size:23px;letter-spacing:.3px}
.card-electrical .service-panel{height:207px;padding:20px 22px 0}
.card-electrical .service-panel p{margin-top:8px;font-size:14.5px;line-height:23px}
.btn-card{display:block;margin-top:14px;width:146px;height:51px;line-height:51px;background:var(--white);color:var(--red)}
.card-led .service-panel,.card-solar .service-panel{height:61px;padding:16px 22px 0}

/* Reviews */
.reviews{position:absolute;left:0;top:1498px;width:1200px;height:542px;background:linear-gradient(180deg,#d8545c 0%,#c93d46 40%,#d85a61 100%);clip-path:polygon(0 92px,100% 0,100% 100%,0 452px)}
.reviews-title{top:1586px;font-size:40px;color:var(--white)}
.avatar{position:absolute;left:541px;top:1665px;width:106px;height:106px;border-radius:50%;background:linear-gradient(180deg,#e9e9ea,#bfc2c6);border:4px solid var(--white)}
.reviewer{position:absolute;left:0;width:1200px;top:1782px;text-align:center;color:var(--white)}
.reviewer strong{font-size:23px;font-weight:700}
.reviewer em{font-size:13px;margin-left:4px}
.stars{position:absolute;left:560px;top:1826px}
.quote{position:absolute;left:200px;width:800px;top:1864px;text-align:center;font-style:italic;font-size:15px;line-height:26px;color:var(--white)}
.dots{position:absolute;left:553px;top:1946px;display:flex;gap:12px}
.dots span{width:9px;height:9px;background:var(--ink)}
.dots span.on{background:transparent;border:2px solid var(--ink)}

/* Client names */
.client{position:absolute;top:2073px;width:184px;height:103px;display:flex;align-items:center;justify-content:center;font-family:"Lato",sans-serif;font-weight:700;font-size:24px;white-space:nowrap}
.client-a{left:96px;color:#c9202a;background:var(--white);font-size:30px}
.client-b{left:376px;background:#fdf100;color:var(--ink);font-size:22px}
.client-c{left:640px;background:#e63027;color:var(--white);font-size:21px}
.client-d{left:905px;background:#d3141b;color:#ffcc00}

/* Footer */
.site-footer{position:absolute;left:0;top:2214px;width:1200px;height:421px;background:linear-gradient(180deg,var(--navy) 0%,#1f1a38 55%,#2a2238 80%,var(--navy-deep) 100%);clip-path:polygon(0 0,100% 86px,100% 100%,0 100%)}
.footer-edge{position:absolute;left:0;top:2208px;width:1200px;height:100px}
.footer-brand{position:absolute;left:78px;top:2280px;display:flex;align-items:center;gap:12px}
.footer-brand .brand-name{color:var(--white)}
.subscribe{position:absolute;left:77px;top:2386px;width:334px;height:50px;border:1px solid var(--red);display:flex}
.subscribe span{flex:1;padding:16px 24px;font-style:italic;font-size:13px;color:#9a97a8}
.subscribe b{width:52px;background:var(--red);display:flex;align-items:center;justify-content:center}
.why-title{position:absolute;left:78px;top:2448px;font-family:"Lato",sans-serif;font-weight:700;font-size:19px;color:var(--red)}
.why-text{position:absolute;left:78px;top:2476px;width:330px;font-size:13.5px;line-height:22px;color:#b9b6c4}
.footer-head{position:absolute;top:2332px;font-family:"Exo 2",sans-serif;font-weight:600;font-size:20px;color:var(--red)}
.quick-links{position:absolute;left:457px;top:2382px;list-style:none}
.quick-links li{font-size:13px;line-height:26px;color:#8d8a9c;padding-left:24px;position:relative}
.quick-links li:first-child{color:var(--white)}
.quick-links li::before{content:"»";position:absolute;left:0;color:var(--red)}
.contact-item{position:absolute;left:676px;color:var(--white)}
.contact-item svg{position:absolute;left:0;top:2px}
.contact-item .txt{position:absolute;left:31px;white-space:nowrap}
.contact-addr .name{font-weight:700;font-size:17px}
.contact-addr .line{font-size:13.5px;line-height:21px;color:#b9b6c4}
.contact-phone .txt{font-size:21px}
.contact-mail .txt{font-size:12px;font-style:italic}
.social{position:absolute;left:934px;display:flex;align-items:center;gap:16px;color:var(--white);font-size:15px}
.social i{display:block;width:42px;height:42px;border-radius:50%;border:2px solid var(--white)}
.social i.solid{background:var(--red);border-color:var(--red)}
.footer-rule{position:absolute;left:0;top:2573px;width:1200px;height:1px;background:#3a3550}
.copyright{position:absolute;left:0;width:1200px;top:2592px;text-align:center;font-family:"Montserrat",sans-serif;font-weight:600;font-size:13px;color:var(--white)}
.copyright span{color:var(--red)}
</style>
</head>
<body>

<header class="site-header">
  <div class="brand"><span class="brand-dot"></span><span class="brand-name">VARNO</span></div>
  <nav class="main-nav">
    <a class="active" href="#" style="left:510px">HOME</a>
    <a href="#" style="left:614px">VARNO STORY</a>
    <a href="#" style="left:768px">PRODUCTS</a>
    <a href="#" style="left:906px">OUR WORK</a>
    <a href="#" style="left:1047px">CONTACT</a>
  </nav>
</header>

<section class="hero">
  <div class="hero-photo" role="img" aria-label="Photo of a long corridor lit by ceiling LED panels"></div>
  <div class="hero-banner"></div>
  <div class="hero-stripe"></div>
  <h2 class="hero-title">Electrical.LED Lighting. Solar Power</h2>
  <p class="hero-sub">Austrealia's largest fully integrated Electrical &amp;<br>Energy Solutions Provider.</p>
</section>

<section class="welcome">
  <div class="welcome-band"></div>
  <div class="welcome-photo" role="img" aria-label="Photo of several LED light bulbs"></div>
  <svg class="welcome-edge" viewBox="0 0 1200 100" width="1200" height="100">
    <polygon points="0,0 1200,88 1200,98 0,10" fill="var(--red)"/>
  </svg>
  <h1 class="welcome-title">Welcome to <span>VARNO</span></h1>
  <p class="welcome-text">Varno Electrical was formed to be an expert Electricity Contracting Company providing services to all Residential and Commercial Customers. With over 10 years of experience, Varno Electrical has developed a highly-experienced team of professionals that ensure all our customer expectations are met.</p>
  <a class="btn btn-welcome" href="#">KNOW MORE</a>
</section>

<section class="services">
  <h2 class="section-title services-title">SERVICES</h2>
  <article class="service-card card-electrical">
    <div class="visual" role="img" aria-label="Photo of an electrician in a hard hat at a switchboard"></div>
    <div class="service-panel">
      <h3>ELECTRICAL</h3>
      <p>Lorem Ipsum is simply dummy text of the printing and typesetting industry. Lorem Ipsum has been the industry's standard.</p>
      <a class="btn btn-card" href="#">KNOW MORE</a>
    </div>
  </article>
  <article class="service-card card-led">
    <div class="visual" role="img" aria-label="Photo of LED spotlight bulbs"></div>
    <div class="service-panel"><h3>LED LIGHTING</h3></div>
  </article>
  <article class="service-card card-solar">
    <div class="visual" role="img" aria-label="Photo of solar panels at sunset"></div>
    <div class="service-panel"><h3>SOLAR POWER</h3></div>
  </article>
</section>

<section class="testimonials">
  <div class="reviews" role="img" aria-label="Red tinted photo of a lit warehouse interior"></div>
  <h2 class="section-title reviews-title">CUSTOMERS Review</h2>
  <div class="avatar" role="img" aria-label="Customer portrait"></div>
  <p class="reviewer"><strong>Dale Morrow,</strong><em>General Manager, Boardline</em></p>
  <svg class="stars" width="84" height="18" viewBox="0 0 84 18">
    <defs>
      <polygon id="star" points="8,0 10.4,5.6 16,6 11.8,9.8 13,16 8,12.8 3,16 4.2,9.8 0,6 5.6,5.6"/>
      <clipPath id="half"><rect x="0" y="0" width="8" height="18"/></clipPath>
    </defs>
    <use href="#star" fill="var(--star)" x="0"/>
    <use href="#star" fill="var(--star)" x="17"/>
    <use href="#star" fill="var(--star)" x="34"/>
    <use href="#star" fill="var(--star)" x="51"/>
    <g transform="translate(68 0)"><use href="#star" fill="var(--star)" clip-path="url(#half)"/></g>
  </svg>
  <p class="quote">"Varno Electrical was pleasantly efficient, cost effective and delivered the desired results we were after. we look forward to seeing an ongoing benefit from dealing with them when we pay the Electrical bill going forward."</p>
  <div class="dots"><span class="on"></span><span></span><span></span><span></span><span></span></div>
</section>

<section class="clients">
  <div class="client client-a">Parkvale</div>
  <div class="client client-b">Outback Supply</div>
  <div class="client client-c">Heron Plumbing</div>
  <div class="client client-d">Golden Grill</div>
</section>

<footer>
  <div class="site-footer" role="img" aria-label="Dark night city skyline photo"></div>
  <svg class="footer-edge" viewBox="0 0 1200 100" width="1200" height="100">
    <polygon points="0,4 1200,90 1200,98 0,12" fill="var(--red)"/>
  </svg>
  <div class="footer-brand"><span class="brand-dot"></span><span class="brand-name">VARNO</span></div>
  <div class="subscribe"><span>E-Mail</span><b><svg width="10" height="14" viewBox="0 0 10 14"><path d="M2 1l6 6-6 6" stroke="#fff" stroke-width="2" fill="none"/></svg></b></div>
  <h4 class="why-title">Why Choose Us?</h4>
  <p class="why-text">Professional service, 5 year workmanship guarantee, Value for Money, Environmentally friendly, Fully insured</p>

  <h4 class="footer-head" style="left:457px">QUICK LINKS</h4>
  <ul class="quick-links">
    <li>Home</li><li>About</li><li>Services</li><li>Contact</li><li>Terms &amp; Conditions</li><li>Privacy Policy</li>
  </ul>

  <h4 class="footer-head" style="left:676px">CONTACT INFO</h4>
  <div class="contact-item contact-addr" style="top:2376px">
    <svg width="20" height="26" viewBox="0 0 20 26"><path d="M10 0C4.5 0 0 4.3 0 9.6 0 16.8 10 26 10 26s10-9.2 10-16.4C20 4.3 15.5 0 10 0z" fill="var(--red)"/><circle cx="10" cy="9.5" r="3.6" fill="var(--navy)"/></svg>
    <div class="txt"><div class="name">VARNO</div><div class="line">12/84 Ashgrove Rd, Glen<br>Corran, VIC 3150</div></div>
  </div>
  <div class="contact-item contact-phone" style="top:2458px">
    <svg width="20" height="20" viewBox="0 0 20 20"><path d="M4 1l4 4-2.5 2.5c1.2 2.8 4 5.6 7 7L15 12l4 4-2.5 3C9 18 2 11 1 3.5z" fill="var(--red)"/></svg>
    <div class="txt">137 604</div>
  </div>
  <div class="contact-item contact-mail" style="top:2504px">
    <svg width="20" height="14" viewBox="0 0 20 14"><rect width="20" height="14" rx="1" fill="var(--red)"/><path d="M1 1l9 7 9-7" stroke="var(--navy)" stroke-width="1.5" fill="none"/></svg>
    <div class="txt">service@varnoelectrical-example.com.au</div>
  </div>

  <h4 class="footer-head" style="left:937px">FOLLOW US</h4>
  <div class="social" style="top:2372px"><i class="solid"></i>Socialhub</div>
  <div class="social" style="top:2430px"><i></i>Chirper</div>
  <div class="social" style="top:2486px"><i></i>Worknet</div>

  <div class="footer-rule"></div>
  <p class="copyright">© <span>VARNO</span> - 2017. All Rights Reserved.</p>
</footer>

</body>
</html>
```